Business Card Makeover. Recreate a sleek modern design for our business card.

DO NOT COPY OUR CURRENT DESIGN. MUST BE ONE SIDED BUSINESS CARD.
Create a new business card design, using our new logo. Attached is a sample of our current design and new logo. Please note the address and email will change. The new address is 412 Corvell Lane Marlow Bay 00401 and our website will be www.delmarhollis.example.

We are an architectural and interior design firm. We prefer a clean modern look. Something that is refined and emulates excellence.

Industry/Entity Type

Architecture

Contact Information for Business Card

clean modern look, please do not copy our attached design.

Font styles to use
Other font styles liked:
• see attached business card font

Colors

Designer to choose colors to be used in the design.

Requirements
Must have
• Must have a modern appeal and resemble our current branding.
Nice to have
• modern font, our logo, legible name and titles progressive design
Should not have
• Do not add colors not reflected in our branding. Should not look like our current card.

```html
<!DOCTYPE html>
<html lang="en">
<head>
<meta charset="utf-8">
<title>Delmar Hollis + Partners — Business Card</title>
<link rel="stylesheet" href="https://fonts.googleapis.com/css2?family=Raleway:wght@300;400;700&display=swap">
<style>
  :root {
    --page-bg: #e9e7e3;
    --card-bg: #f7f7f6;
    --brand-blue: #1565b5;
    --brand-blue-light: #2f7fcc;
    --ink: #2b2b2b;
    --ink-soft: #555;
  }
  * { box-sizing: border-box; margin: 0; padding: 0; }
  html, body {
    width: 1200px; height: 1022px; overflow: hidden;
    background: var(--page-bg);
    font-family: "Raleway", Arial, sans-serif;
  }
  .card {
    position: absolute;
    left: 75px; top: 211px;
    width: 1050px; height: 600px;
    background: var(--card-bg);
    box-shadow: 0 6px 24px rgba(0,0,0,.12);
  }
  .brand {
    position: absolute; left: 48px; top: 52px;
    display: flex; align-items: center; gap: 14px;
  }
  .brand-mark {
    width: 62px; height: 62px; border-radius: 50%;
    background: var(--brand-blue);
  }
  .brand-name {
    font-weight: 400; font-size: 40px; letter-spacing: 1px;
    color: var(--ink); line-height: 1;
  }
  .brand-sub {
    display: block; font-size: 11px; letter-spacing: 6px;
    color: var(--ink-soft); text-align: right; margin-top: 6px;
  }
  .name-band {
    position: absolute; left: 470px; right: 0; top: 44px; height: 86px;
    background: var(--brand-blue);
    padding: 14px 28px; color: #fff;
  }
  .person-name { font-weight: 700; font-size: 27px; letter-spacing: 1px; }
  .person-title { font-weight: 300; font-size: 24px; margin-top: 2px; }
  .details {
    position: absolute; left: 498px; top: 160px;
    color: var(--ink); font-weight: 300; font-size: 25px; line-height: 1.2;
  }
  .address { margin-bottom: 14px; }
  .contact-list { list-style: none; }
  .contact-list li { display: flex; align-items: center; gap: 12px; height: 33px; }
  .contact-list svg { width: 20px; height: 20px; flex: none; fill: none; stroke: var(--brand-blue); stroke-width: 2; }
  .services { margin-top: 22px; }
  .license { color: var(--brand-blue-light); font-weight: 400; }
</style>
</head>
<body>
  <div class="card">
    <div class="brand">
      <span class="brand-mark"></span>
      <div class="brand-name">DELMARHOLLIS<span class="brand-sub">+ PARTNERS</span></div>
    </div>

    <div class="name-band">
      <div class="person-name">WARREN ASHBY</div>
      <div class="person-title">Partner/ Director of Design</div>
    </div>

    <div class="details">
      <p class="address">412 Corvell Lane<br>Marlow Bay 00401</p>
      <ul class="contact-list">
        <li><svg viewBox="0 0 20 20" aria-hidden="true"><circle cx="10" cy="10" r="8.5"/><path d="M7 6.5c0 4 2.5 6.8 6.5 7l.5-2-2-1-1 1c-1-.5-2-1.5-2.5-2.5l1-1-1-2z" fill="#1565b5" stroke="none"/></svg>555.014.2276</li>
        <li><svg viewBox="0 0 20 20" aria-hidden="true"><rect x="5" y="2.5" width="10" height="5"/><rect x="2.5" y="7.5" width="15" height="7"/><rect x="5" y="12" width="10" height="5.5"/></svg>555.014.3381</li>
        <li><svg viewBox="0 0 20 20" aria-hidden="true"><rect x="6" y="2" width="8" height="16" rx="1.5"/><path d="M9 15.5h2"/></svg>555.019.4402</li>
        <li><svg viewBox="0 0 20 20" aria-hidden="true"><rect x="2" y="4.5" width="16" height="11"/><path d="M2 4.5l8 6.5 8-6.5"/></svg>warren@delmarhollis.example</li>
        <li><svg viewBox="0 0 20 20" aria-hidden="true"><circle cx="10" cy="10" r="8"/><path d="M2 10h16M10 2c-3 3-3 13 0 16M10 2c3 3 3 13 0 16"/></svg>www.delmarhollis.example</li>
      </ul>
      <p class="services">Architecture + Interior Design</p>
      <p class="license">LIC# AA10004821</p>
    </div>
  </div>
</body>
</html>
```